Web Site Mock Up's for a Dog Food Business

We are a supplier of bespoke dog food. We tailor our dog food to meet the dogs needs.We are looking for ideas (mock ups) of design ideas for our new web site - Just mock ups - web site will follow if we are happy with the mock ups.I have included our logo (PSD file). I have also included a rough (please don’t copy) home page with the information we would ideally like on the page. Note the page will have sliders at the top, we have done two example sliders, and included a video to be included.I have also enclosed the questions we need to find out in order to develop a dogs food.I would like to see a home page, and a tell us about your dog page.Would like mock ups as PSD files, so we can play around with.I am open to ideas and better designs. DO NOT JUST COPY MY LAYOUTSome of our competitors sites include www.tails.comwww.paws.comwww.parcelpet.comwww.growlingtums.co.ukI want a clean, bright easy to navigate site. Happy to play around with colours - doesn’t have to be the browns I have used. Happy to use both infographics and photo of real dogs, but I do want site to look like the best food available for dogs.Web site will be a database driven site, with around 10 -15 pages plus about 60 dynamic database driven pages of products (all same layout )Look forward to receiving your ideas.

```html
<!DOCTYPE html>
<html lang="en">
<head>
<meta charset="utf-8">
<title>Bowlcraft – Home</title>
<link rel="stylesheet" href="https://fonts.googleapis.com/css2?family=Poppins:wght@400;600;700;800&family=Quicksand:wght@500;600;700&display=swap">
<style>
:root{
  --brown-dark:#3b1a0f;
  --brown-btn:#4a2114;
  --brown-social:#6e3522;
  --hero-grey:#6e6c6a;
  --header-grey:rgba(70,68,66,.55);
  --text-grey:#555;
  --footer-bg:#1e1e1e;
  --white:#fff;
}
*{margin:0;padding:0;box-sizing:border-box}
html,body{width:1200px;height:3046px;overflow:hidden}
body{font-family:'Quicksand',sans-serif;color:var(--text-grey);background:var(--white);position:relative}
.abs{position:absolute}
.center-x{left:0;width:1200px;text-align:center}

/* hero */
.hero{position:absolute;top:0;left:0;width:1200px;height:716px;background:radial-gradient(ellipse at 55% 45%,#8d8884 0%,#6e6a67 45%,#555250 100%)}
.hero-photo{position:absolute;inset:0}
.topbar{position:absolute;top:0;left:0;width:1200px;height:50px;font-family:'Poppins',sans-serif;font-size:15px;color:var(--white)}
.topbar span{position:absolute;top:13px;display:flex;align-items:center;gap:7px}
.flag{width:14px;height:10px;background:#c8ccd6;display:inline-block}
.header{position:absolute;top:50px;left:0;width:1200px;height:82px;background:var(--header-grey)}
.brand{position:absolute;left:118px;top:25px;font-family:'Poppins',sans-serif;font-weight:700;font-size:22px;color:var(--white);display:flex;align-items:center;gap:8px}
.brand i{width:14px;height:14px;border-radius:50%;background:var(--white);display:inline-block}
.nav{position:absolute;top:27px;font-family:'Poppins',sans-serif;font-size:17px;color:var(--white)}
.hero-title{top:322px;font-family:'Poppins',sans-serif;font-weight:800;font-size:64px;line-height:76px;color:var(--white);letter-spacing:2px}
.hero-sub{top:402px;font-family:'Poppins',sans-serif;font-size:28px;line-height:44px;color:var(--white)}
.btn{position:absolute;display:flex;align-items:center;justify-content:center;background:var(--brown-btn);color:var(--white);font-family:'Poppins',sans-serif;font-weight:700;border-radius:26px}
.follow{position:absolute;left:38px;top:282px;width:24px}
.follow i{display:block;width:14px;height:14px;border-radius:3px;background:var(--white);margin:0 auto 30px}
.follow .line{width:2px;height:50px;background:var(--white);margin:0 auto}
.follow-text{position:absolute;left:20px;top:545px;transform:rotate(-90deg);transform-origin:left top;font-family:'Poppins',sans-serif;font-size:16px;color:var(--white);white-space:nowrap}
.dot{position:absolute;border-radius:50%;background:var(--white)}

/* steps */
.section-title{position:absolute;left:0;width:1200px;text-align:center;font-family:'Poppins',sans-serif;font-weight:700;color:var(--brown-dark)}
.step-circle{position:absolute;width:146px;height:146px;border-radius:50%;background:var(--brown-dark);display:flex;align-items:center;justify-content:center}
.step-num{position:absolute;right:-2px;bottom:-4px;width:30px;height:30px;border-radius:50%;background:#2d2d2d;border:3px solid var(--white);color:var(--white);font-family:'Poppins',sans-serif;font-size:14px;display:flex;align-items:center;justify-content:center}
.step-label{position:absolute;width:300px;text-align:center;font-family:'Poppins',sans-serif;font-weight:700;font-size:21px;line-height:36px;color:var(--brown-dark);text-transform:uppercase}
.step-text{position:absolute;width:262px;text-align:center;font-size:15px;line-height:27px;color:var(--text-grey)}

/* foods */
.foods{position:absolute;top:1295px;left:0;width:1200px;height:806px;background:linear-gradient(180deg,#e2e0dd,#ecebea 50%,#e4e2df)}
.foods-desc{top:1424px;font-size:16.5px;line-height:31px;color:#333}
.tile{position:absolute;width:321px;height:207px}
.tile-card{background:var(--brown-dark);color:var(--white);text-align:center}
.tile-card .frame{position:absolute;inset:8px;border:1.5px dashed #c9a98f}
.tile-card h3{position:absolute;top:16px;left:0;width:100%;font-family:'Poppins',sans-serif;font-weight:700;font-size:22px;line-height:32px}
.tile-card .rule{position:absolute;top:52px;left:92px;width:137px;height:2px;background:var(--white)}
.tile-card p{position:absolute;top:62px;left:22px;width:277px;font-family:'Poppins',sans-serif;font-size:11.5px;line-height:22px}
.tile-card .more{position:absolute;top:158px;left:104px;width:114px;height:30px;border-radius:15px;background:var(--white);color:var(--brown-dark);font-family:'Poppins',sans-serif;font-weight:600;font-size:13px;line-height:30px}

/* testimonials */
.testimonials{position:absolute;top:2101px;left:0;width:1200px;height:482px;background:radial-gradient(ellipse at 50% 60%,#8a5a40 0%,#6d4330 55%,#583425 100%)}
.quote-text{top:2242px;font-size:16.5px;line-height:32px;color:var(--white)}
.quote-mark{position:absolute;font-family:'Poppins',sans-serif;font-weight:800;font-size:90px;line-height:1;color:var(--white)}
.avatar{position:absolute;border-radius:50%;background:linear-gradient(180deg,#9d9a98,#6e6b69);border:3px solid rgba(255,255,255,.55)}
.avatar.active{border:4px solid var(--white);background:linear-gradient(180deg,#b5aea8,#7e746d)}

/* footer */
.footer{position:absolute;top:2583px;left:0;width:1200px;height:463px;background:var(--footer-bg)}
.footer-brand{top:2700px;font-family:'Poppins',sans-serif;font-weight:700;font-size:40px;color:var(--white)}
.contact-row{position:absolute;top:2813px;left:0;width:1200px;display:flex;justify-content:center;gap:38px;font-family:'Poppins',sans-serif;font-size:16px;color:var(--white)}
.contact-row span{display:flex;align-items:center;gap:8px}
.social{position:absolute;width:42px;height:42px;border-radius:50%;background:var(--brown-social);border:2px solid rgba(255,255,255,.25)}
.footer-links{top:2935px;font-family:'Poppins',sans-serif;font-size:16.5px;color:var(--white);word-spacing:2px}
.copyright{top:2985px;font-family:'Poppins',sans-serif;font-size:16px;color:var(--white)}
</style>
</head>
<body>

<!-- Hero -->
<section class="hero">
  <div class="hero-photo" role="img" aria-label="Photo of a beagle eating from a steel bowl"></div>
  <div class="topbar">
    <span style="left:456px"><svg width="13" height="13" viewBox="0 0 24 24"><path fill="#fff" d="M6.6 10.8a15 15 0 0 0 6.6 6.6l2.2-2.2c.3-.3.7-.4 1-.2 1.1.4 2.3.6 3.6.6.6 0 1 .4 1 1V20c0 .6-.4 1-1 1A17 17 0 0 1 3 4c0-.6.4-1 1-1h3.5c.6 0 1 .4 1 1 0 1.3.2 2.5.6 3.6.1.3 0 .7-.2 1z"/></svg>555 014 2290</span>
    <span style="left:608px"><svg width="14" height="11" viewBox="0 0 24 18"><path fill="#fff" d="M0 0h24v18H0z"/><path fill="none" stroke="#6e6c6a" stroke-width="2" d="M1 1l11 9 11-9"/></svg>info@bowlcraft.co.uk</span>
    <span style="left:830px"><svg width="12" height="13" viewBox="0 0 24 26"><circle cx="12" cy="7" r="6" fill="#fff"/><path fill="#fff" d="M0 26c0-7 5-11 12-11s12 4 12 11z"/></svg>login</span>
    <span style="left:906px"><svg width="13" height="13" viewBox="0 0 24 24"><path fill="#fff" d="M23 1L1 10l10 3 3 10z"/></svg>Contact Us</span>
    <span style="left:1026px"><i class="flag"></i>English<svg width="9" height="6" viewBox="0 0 10 6"><path fill="none" stroke="#fff" stroke-width="2" d="M1 1l4 4 4-4"/></svg></span>
  </div>
  <header class="header">
    <div class="brand"><i></i>bowlcraft.co.uk</div>
    <span class="nav" style="left:512px">Home</span>
    <span class="nav" style="left:586px">Our Food</span>
    <span class="nav" style="left:686px">How it Works</span>
    <span class="nav" style="left:815px">Pricing</span>
    <span class="nav" style="left:897px">Customer Reviews</span>
    <span class="nav" style="left:1076px">FAQ</span>
  </header>

  <svg class="abs" style="left:576px;top:271px" width="48" height="48" viewBox="0 0 48 48"><circle cx="24" cy="24" r="22" fill="none" stroke="#fff" stroke-width="2"/><path fill="none" stroke="#fff" stroke-width="2" d="M19 15l13 9-13 9z"/></svg>
  <div class="abs center-x hero-title">BOWLCRAFT</div>
  <div class="abs center-x hero-sub">Food unique as your dog blended using the<br>finest ingredients</div>
  <div class="btn" style="left:480px;top:507px;width:240px;height:50px;font-size:18px">Tell Us About Your Dog</div>

  <div class="follow"><i></i><i></i><i></i><i></i><div class="line"></div></div>
  <div class="follow-text">Follow us</div>

  <div class="dot" style="left:1149px;top:389px;width:12px;height:12px"></div>
  <svg class="abs" style="left:1141px;top:419px" width="28" height="28" viewBox="0 0 28 28"><circle cx="14" cy="14" r="12" fill="none" stroke="#fff" stroke-width="2.5"/><circle cx="14" cy="14" r="7" fill="#fff"/></svg>
  <div class="dot" style="left:1149px;top:463px;width:12px;height:12px"></div>
</section>

<!-- How It Works -->
<section>
  <h2 class="section-title" style="top:796px;font-size:36px">How It Works</h2>

  <div class="step-circle" style="left:167px;top:895px">
    <svg width="60" height="70" viewBox="0 0 60 70" fill="none" stroke="#fff" stroke-width="3"><path d="M8 4h30l14 14v48H8z"/><path d="M38 4v14h14"/><rect x="16" y="26" width="26" height="18"/><path d="M16 52h28M16 58h20"/></svg>
    <span class="step-num">1</span>
  </div>
  <div class="step-circle" style="left:527px;top:895px">
    <svg width="76" height="60" viewBox="0 0 76 60" fill="none" stroke="#fff" stroke-width="3"><circle cx="26" cy="14" r="5"/><circle cx="38" cy="10" r="5"/><circle cx="50" cy="14" r="5"/><path d="M4 24h68l-8 32H12z"/><path d="M26 38h24M24 34a3 3 0 1 0 0 8M52 34a3 3 0 1 1 0 8"/></svg>
    <span class="step-num">2</span>
  </div>
  <div class="step-circle" style="left:894px;top:895px">
    <svg width="86" height="60" viewBox="0 0 86 60" fill="none" stroke="#fff" stroke-width="3"><path d="M4 6h50v40H4zM54 18h16l12 14v14H54"/><circle cx="18" cy="48" r="6" fill="#3b1a0f"/><circle cx="68" cy="48" r="6" fill="#3b1a0f"/><path d="M18 26l8 8 16-16"/></svg>
    <span class="step-num">3</span>
  </div>

  <svg class="abs" style="left:332px;top:952px" width="175" height="32" viewBox="0 0 175 32"><path d="M0 16h132" stroke="#7b5e52" stroke-width="4" stroke-dasharray="10 8"/><path fill="#7b5e52" d="M130 2l45 14-45 14 10-14z"/></svg>
  <svg class="abs" style="left:700px;top:952px" width="175" height="32" viewBox="0 0 175 32"><path d="M0 16h132" stroke="#7b5e52" stroke-width="4" stroke-dasharray="10 8"/><path fill="#7b5e52" d="M130 2l45 14-45 14 10-14z"/></svg>

  <div class="step-label" style="left:92px;top:1053px">Tell us about<br>your dog</div>
  <div class="step-label" style="left:446px;top:1053px">We create your<br>food</div>
  <div class="step-label" style="left:820px;top:1053px">We delivery</div>

  <p class="step-text" style="left:112px;top:1125px">Sed ut perspiciatis unde omnis iste natus error sit voluptatem accusan-tium doloremque laudantium</p>
  <p class="step-text" style="left:470px;top:1125px">Sed ut perspiciatis unde omnis iste natus error sit voluptatem accusan-tium doloremque laudantium</p>
  <p class="step-text" style="left:839px;top:1125px">Sed ut perspiciatis unde omnis iste natus error sit voluptatem accusan-tium doloremque laudantium</p>
</section>

<!-- Our Foods -->
<section class="foods" role="img" aria-label="Light wooden table background with scattered kibble"></section>
<h2 class="section-title" style="top:1354px;font-size:34px">OUR FOODS</h2>
<p class="abs center-x foods-desc">We develop and create your dogs ideal food using the finest ingredients, based on your dogs<br>requirements.</p>

<div class="tile" style="left:90px;top:1505px;background:linear-gradient(135deg,#3a2a20,#6a4a36 55%,#3e2c22)" role="img" aria-label="Photo of a bowl of kibble on a dark wooden table"></div>
<div class="tile tile-card" style="left:440px;top:1505px">
  <div class="frame"></div>
  <h3>ADULT FOOD</h3>
  <div class="rule"></div>
  <p>Careful balance of proteins, fats and oils, minerals, vitamins &amp; carbohydrates are needed as an adult and differ between breeds</p>
  <div class="more">Tell me more</div>
</div>
<div class="tile" style="left:789px;top:1505px;background:linear-gradient(180deg,#f4f2ef,#e6d3b4 60%,#c98a5e)" role="img" aria-label="Photo of a puppy in a chef hat beside fresh ingredients"></div>
<div class="tile" style="left:90px;top:1733px;background:linear-gradient(160deg,#e9e6e1,#d4b78c 55%,#a7a29c)" role="img" aria-label="Photo of a dog eating from a steel bowl"></div>
<div class="tile" style="left:440px;top:1733px;background:linear-gradient(180deg,#ecebea,#c9b49a 55%,#b9b8b6)" role="img" aria-label="Photo of a pug sitting behind a bowl of food"></div>
<div class="tile" style="left:789px;top:1733px;background:linear-gradient(135deg,#4a3124,#8a5b3c 55%,#5a3a29)" role="img" aria-label="Photo of dog paws beside a bowl of kibble on wood"></div>

<div class="btn" style="left:522px;top:1981px;width:156px;height:46px;font-size:17px">Start Now</div>

<!-- Testimonials -->
<section class="testimonials" role="img" aria-label="Photo of a long-haired dog resting, tinted brown"></section>
<h2 class="abs center-x" style="top:2155px;font-family:'Poppins',sans-serif;font-weight:700;font-size:33px;color:#fff">TESTIMONIALS</h2>
<div class="quote-mark" style="left:192px;top:2222px">&ldquo;</div>
<p class="abs center-x quote-text">I have 3 dogs all on different foods.&nbsp;&nbsp;&nbsp;&nbsp;&nbsp;&nbsp;&nbsp;No more trips to the shops fetching massive bags of<br>food. This works for me and my dogs love it. - <b>Mara with Tobin - Wrenfield</b>.</p>
<div class="quote-mark" style="left:950px;top:2296px">&rdquo;</div>

<svg class="abs" style="left:162px;top:2393px" width="28" height="42" viewBox="0 0 28 42"><path d="M24 3L6 21l18 18" fill="none" stroke="#fff" stroke-width="4"/></svg>
<div class="avatar" style="left:262px;top:2370px;width:86px;height:86px" role="img" aria-label="Customer portrait"></div>
<div class="avatar" style="left:396px;top:2370px;width:86px;height:86px" role="img" aria-label="Customer portrait"></div>
<div class="avatar active" style="left:546px;top:2359px;width:108px;height:108px" role="img" aria-label="Customer portrait"></div>
<div class="avatar" style="left:719px;top:2370px;width:86px;height:86px" role="img" aria-label="Customer portrait"></div>
<div class="avatar" style="left:853px;top:2370px;width:86px;height:86px" role="img" aria-label="Customer portrait"></div>
<svg class="abs" style="left:1003px;top:2393px" width="28" height="42" viewBox="0 0 28 42"><path d="M4 3l18 18L4 39" fill="none" stroke="#fff" stroke-width="4"/></svg>

<div class="abs" style="left:180px;top:2514px;width:842px;height:1px;background:rgba(255,255,255,.4)"></div>
<div class="abs" style="left:555px;top:2512px;width:90px;height:5px;background:#fff"></div>

<!-- Footer -->
<footer class="footer"></footer>
<div class="abs center-x footer-brand">bowlcraft.co.uk</div>
<div class="contact-row">
  <span><svg width="14" height="14" viewBox="0 0 24 24"><path fill="#fff" d="M23 1L1 10l10 3 3 10z"/></svg>82 Larkspur Lane Ashford</span>
  <span><svg width="13" height="13" viewBox="0 0 24 24"><path fill="#fff" d="M6.6 10.8a15 15 0 0 0 6.6 6.6l2.2-2.2c.3-.3.7-.4 1-.2 1.1.4 2.3.6 3.6.6.6 0 1 .4 1 1V20c0 .6-.4 1-1 1A17 17 0 0 1 3 4c0-.6.4-1 1-1h3.5c.6 0 1 .4 1 1 0 1.3.2 2.5.6 3.6.1.3 0 .7-.2 1z"/></svg>Phone: +(555) 014-2290</span>
  <span><svg width="15" height="11" viewBox="0 0 24 18"><path fill="#fff" d="M0 0h24v18H0z"/><path fill="none" stroke="#1e1e1e" stroke-width="2" d="M1 1l11 9 11-9"/></svg>Email: info@bowlcraft.co.uk</span>
</div>
<div class="social" style="left:549px;top:2862px" role="img" aria-label="Social link"></div>
<div class="social" style="left:607px;top:2862px" role="img" aria-label="Social link"></div>
<p class="abs center-x footer-links">Home&nbsp;&nbsp;|&nbsp;&nbsp;Our Food&nbsp;&nbsp;|&nbsp;&nbsp;How it Works&nbsp;&nbsp;|&nbsp;&nbsp;Pricing&nbsp;&nbsp;|&nbsp;&nbsp;Customer Reviews&nbsp;&nbsp;|&nbsp;&nbsp;FAQ&nbsp;&nbsp;|&nbsp;&nbsp;Contact Us</p>
<p class="abs center-x copyright">Copyright © 2018. All Rights Reserved.</p>

</body>
</html>
```